Realty Group Needs Classy, Contemporary Letterhead Design

We need a letterhead design for a new realty company located in NY, USA. We buy investment properties to rehabilitate and or keep in our rental portfolio.

```html
<!DOCTYPE html>
<html lang="en">
<head>
<meta charset="utf-8">
<title>Meridale Realty Group Letterhead</title>
<link href="https://fonts.googleapis.com/css2?family=Arimo:wght@400;700&display=swap" rel="stylesheet">
<style>
  :root {
    --backdrop: #c4c4c4;
    --paper: #ffffff;
    --brand-purple: #4b2a7f;
    --brand-purple-soft: #6a4a9c;
    --ink: #1e1e1e;
    --muted: #8a8a8a;
    --rule: #9a9a9a;
  }
  * { box-sizing: border-box; margin: 0; padding: 0; }
  html, body {
    width: 1200px;
    height: 1089px;
    overflow: hidden;
    background: var(--backdrop);
    font-family: "Arimo", Arial, sans-serif;
  }
  .sheet-row {
    position: absolute;
    left: 25px;
    top: 182px;
    display: flex;
    gap: 30px;
  }
  .sheet {
    position: relative;
    width: 560px;
    height: 725px;
    box-shadow: 0 10px 26px rgba(0,0,0,0.2);
  }
  .sheet-front {
    background: var(--paper);
    color: var(--ink);
    padding: 44px 52px 40px;
  }
  .sheet-back { background: var(--brand-purple); }

  .brand {
    display: flex;
    justify-content: flex-end;
  }
  .brand-lockup {
    display: flex;
    align-items: center;
    gap: 7px;
    padding-bottom: 6px;
    border-bottom: 1px solid var(--rule);
  }
  .brand-mark {
    width: 10px;
    height: 10px;
    border-radius: 50%;
    background: var(--brand-purple);
  }
  .brand-name {
    font-size: 17px;
    font-weight: 700;
    color: var(--brand-purple);
  }
  .letter-date {
    text-align: right;
    font-size: 10px;
    margin-top: 22px;
  }
  .recipient {
    font-style: normal;
    font-size: 10px;
    line-height: 1.45;
    margin: 16px 0 0 140px;
  }
  .recipient-name { font-weight: 700; }
  .letter-body {
    margin-top: 22px;
    font-size: 10px;
    line-height: 1.5;
  }
  .salutation { margin-bottom: 1px; }
  .paragraph {
    text-align: justify;
    margin-bottom: 10px;
  }
  .signature {
    display: block;
    width: 88px;
    height: 22px;
    margin: 10px 0 3px;
  }
  .sender-name {
    font-weight: 700;
    font-size: 11.5px;
  }
  .contact-list {
    position: absolute;
    left: 52px;
    bottom: 40px;
    list-style: none;
    font-size: 9.5px;
    color: var(--muted);
    line-height: 1.6;
  }
  .contact-list li { display: flex; align-items: center; gap: 6px; }
  .contact-icon { width: 8px; height: 8px; flex: none; }

  .watermark {
    position: absolute;
    left: 200px;
    bottom: 40px;
    width: 160px;
    height: 140px;
    border-radius: 12px;
    background: radial-gradient(ellipse at center, var(--brand-purple-soft) 0%, rgba(106,74,156,0) 72%);
    opacity: 0.8;
  }
</style>
</head>
<body>
  <div class="sheet-row">
    <main class="sheet sheet-front">
      <header class="brand">
        <div class="brand-lockup">
          <span class="brand-mark"></span>
          <span class="brand-name">Meridale Realty Group, LLC</span>
        </div>
      </header>

      <p class="letter-date">4th September 20XX</p>

      <address class="recipient">
        <span class="recipient-name">Ronny Reader</span><br>
        CEO, Company Name<br>
        123 Address St<br>
        Anytown, ST 12345
      </address>

      <section class="letter-body">
        <p class="salutation">Dear Mr. Reader,</p>
        <p class="paragraph">Lorem ipsum dolor sit amet, consectetuer adipiscing elit, sed diam nonummy nibh euismod tincidunt ut laoreet dolore magna aliquam erat volutpat. Ut wisi enim ad minim veniam, quis nostrud exerci tation ullamcorper suscipit lobortis nisl ut aliquip ex ea commodo consequat.</p>
        <p class="paragraph">Duis autem vel eum iriure dolor in hendrerit in vulputate velit esse molestie consequat, vel illum dolore eu feugiat nulla facilisis at vero eros et accumsan.</p>
        <p class="paragraph">Nam liber tempor cum soluta nobis eleifend option congue nihil imperdiet doming id quod mazim placerat facer possim assum. Typi non habent claritatem insitam; est usus legentis in iis qui facit eorum claritatem. Investigationes demonstraverunt lectores legere me lius quod ii legunt saepius.</p>
        <p class="closing">Sincerely,</p>
        <svg class="signature" viewBox="0 0 88 22" role="img" aria-label="Handwritten signature">
          <rect x="0" y="5" width="88" height="12" rx="6" fill="#ececec"/>
        </svg>
        <p class="sender-name">Your Name</p>
      </section>

      <ul class="contact-list">
        <li>
          <svg class="contact-icon" viewBox="0 0 12 12"><path d="M3 1 L5 3.5 L4 5 Q5.5 7 7 8 L8.5 7 L11 9 L9.5 11 Q5 10.5 1 3 Z" fill="var(--brand-purple)"/></svg>
          (555) 014-2290
        </li>
        <li>
          <svg class="contact-icon" viewBox="0 0 12 12"><rect x="0.5" y="2.5" width="11" height="7.5" fill="var(--brand-purple)"/><path d="M0.5 2.5 L6 7 L11.5 2.5" stroke="#fff" stroke-width="1" fill="none"/></svg>
          info@meridalerealty.com
        </li>
        <li>
          <svg class="contact-icon" viewBox="0 0 12 12"><path d="M6 0.5 A4 4 0 0 1 10 4.5 C10 7.5 6 11.5 6 11.5 C6 11.5 2 7.5 2 4.5 A4 4 0 0 1 6 0.5 Z" fill="var(--brand-purple)"/><circle cx="6" cy="4.5" r="1.5" fill="#fff"/></svg>
          www.meridalerealty.com
        </li>
      </ul>
    </main>

    <section class="sheet sheet-back" aria-label="Reverse side of letterhead">
      <div class="watermark" role="img" aria-label="Faint archer silhouette watermark"></div>
    </section>
  </div>
</body>
</html>
```